Halvery Construction Group Website

Need a dynamic corporate website that can be built on with time. We want to get our information out to the world and have a place where customers can submit requests for proposals.

Target Market(s)

Custom home owners and buyers. Architects and Real Estate Agents.

Industry/Entity Type

Construction

Number of Pages Required

3 page

Font styles to use
Serif
Sans Serif

Requirements
Must have
• Company logo, about, company contact information, biography, contact, projects,
• Sleek, modern, clean, attractive design.
• Online form customers can use for filling out a request for project proposal.
• Linkedin hyperlink.
• Uses www.halveryconstructiongroup.example

```html
<!DOCTYPE html>
<html lang="en">
<head>
<meta charset="utf-8">
<title>Halvery Construction Group</title>
<link href="https://fonts.googleapis.com/css2?family=Ubuntu:wght@400;500;700&family=Open+Sans:wght@400;600&display=swap" rel="stylesheet">
<style>
:root{
  --blue:#0d4c9a;
  --blue-deep:#0a2f7a;
  --tile-blue:#0b3fa6;
  --white:#ffffff;
  --text:#555555;
  --grey:#777777;
  --icon:#8a8a8a;
}
*{margin:0;padding:0;box-sizing:border-box}
html,body{width:1189px;height:1200px;overflow:hidden;background:var(--white)}
body{font-family:"Open Sans",sans-serif;color:var(--text);position:relative}
.hero{position:absolute;left:0;top:0;width:1189px;height:489px;
  background:linear-gradient(180deg,#9a7f63 0%,#8c8579 30%,#7d7a72 60%,#6d6253 100%)}
.hero-shade{position:absolute;inset:0;background:rgba(40,35,30,.25)}
.brand{position:absolute;left:74px;top:29px;display:flex;align-items:center;gap:10px;color:var(--white);font-family:"Ubuntu",sans-serif;font-weight:500}
.brand-mark{width:54px;height:52px;background:var(--white);border-radius:4px}
.brand-name{line-height:1}
.brand-name .big{display:block;font-size:33px;letter-spacing:1px}
.brand-name .small{display:block;font-size:10px;margin-top:3px;letter-spacing:.2px}
.nav{position:absolute;top:47px;left:585px;display:flex;gap:27px;font-family:"Ubuntu",sans-serif;font-weight:500;font-size:14px;color:var(--white)}
.menu-toggle{position:absolute;left:1093px;top:43px}
.hero-copy{position:absolute;left:0;width:1189px;top:204px;text-align:center;color:var(--white);font-family:"Ubuntu",sans-serif}
.hero-copy h1{font-size:58px;font-weight:700;letter-spacing:1px;line-height:1.05}
.hero-copy p{font-size:20px;font-weight:500;line-height:27px;margin:12px auto 0;width:560px}
.dots{position:absolute;top:444px;left:573px;display:flex;gap:5px}
.dots span{width:12px;height:12px;border-radius:50%;background:var(--white)}
.dots span.active{background:#2b8ad6}
.welcome{position:absolute;left:74px;top:532px;width:300px}
.welcome h2{font-family:"Ubuntu",sans-serif;font-weight:400;font-size:22px;color:var(--blue);letter-spacing:.3px}
.welcome p{font-size:14px;line-height:25px;margin-top:9px}
.btn{position:absolute;left:74px;top:689px;width:130px;height:42px;background:linear-gradient(180deg,#1a64b8,#0c4b97);
  color:var(--white);font-family:"Ubuntu",sans-serif;font-weight:500;font-size:14px;letter-spacing:.5px;display:flex;align-items:center;justify-content:center}
.tile{position:absolute;top:538px;width:228px;height:193px;display:flex;align-items:center;justify-content:center;
  color:var(--white);font-family:"Ubuntu",sans-serif;font-size:22px}
.tile.commercial{left:416px;background:linear-gradient(160deg,#0b3a8f,#062a70)}
.tile.residential{left:653px;background:linear-gradient(160deg,#1550b4,#0c3f9a)}
.tile.community{left:889px;background:linear-gradient(160deg,#0f47b0,#0b3ea0)}
.feature{position:absolute;top:774px;height:310px;width:595px;color:var(--white);text-align:center;padding-top:96px}
.feature.bio{left:0;background:linear-gradient(160deg,#b9c0cc,#8f97a6 60%,#a49a70)}
.feature.projects{left:595px;width:594px;background:linear-gradient(180deg,#2b4c92,#3a5490 50%,#6b5a55)}
.feature h3{font-family:"Ubuntu",sans-serif;font-weight:400;font-size:22px}
.feature p{font-size:14px;line-height:25px;width:450px;margin:6px auto 0}
.footer-nav{position:absolute;left:74px;top:1116px;display:flex;gap:31px;font-family:"Ubuntu",sans-serif;font-size:15px;color:var(--blue)}
.copyright{position:absolute;left:74px;top:1148px;font-size:12.5px;color:var(--grey)}
.follow{position:absolute;left:940px;top:1118px;font-family:"Ubuntu",sans-serif;font-size:15px;color:#333}
.social{position:absolute;left:940px;top:1142px;display:flex;gap:22px}
.social span{width:18px;height:18px;border-radius:50%;background:var(--icon)}
</style>
</head>
<body>
<header class="hero">
  <div class="hero-shade" role="img" aria-label="Photo of four builders in hard hats and safety vests reviewing plans inside a block-walled building under construction"></div>
  <div class="brand">
    <div class="brand-mark"></div>
    <div class="brand-name"><span class="big">HALVERY</span><span class="small">CONSTRUCTION GROUP, INC.</span></div>
  </div>
  <nav class="nav"><span>HOME</span><span>ABOUT</span><span>BIO</span><span>PROJECTS</span><span>CONTACT US</span></nav>
  <svg class="menu-toggle" width="24" height="24" viewBox="0 0 24 24"><rect x="1" y="1" width="22" height="22" rx="3" fill="none" stroke="#fff" stroke-width="2"/><path d="M12 6v12M6 12h12" stroke="#fff" stroke-width="2"/></svg>
  <div class="hero-copy">
    <h1>FUSCE ACCUMSAN</h1>
    <p>Vestibulum ante ipsum primis in faucibus orci luctus et ultrices posuere cubilia</p>
  </div>
  <div class="dots"><span class="active"></span><span></span><span></span></div>
</header>

<section class="welcome">
  <h2>WELCOME TO OUR WEBSITE</h2>
  <p>Aliquam molestie, mi et imperdiet euismod, dui purus auctor tellus, et interdum lacus lectus et ante. Sed accumsan sollicitudin sapien, sit amet adipiscing turpis gravida ac.</p>
</section>
<a class="btn">READ MORE</a>

<div class="tile commercial" role="img" aria-label="Blue-tinted photo of a commercial building frame">COMMERCIAL</div>
<div class="tile residential" role="img" aria-label="Blue-tinted photo of a house model on blueprints">RESIDENTIAL</div>
<div class="tile community" role="img" aria-label="Blue-tinted photo of hands reviewing plans">COMMUNITY</div>

<section class="feature bio" role="img" aria-label="Soft photo of blueprints, a hard hat and a tape measure with colleagues behind">
  <h3>BIO</h3>
  <p>Aliquam molestie, mi et imperdiet euismod, dui purus auctor tellus, et interdum lacus lectus et ante. Sed accumsan sollicitudin sapien, sit amet adipiscing turpis gravida ac.</p>
</section>
<section class="feature projects" role="img" aria-label="Blue-tinted photo of cranes over an apartment block under construction">
  <h3>OUR PROJECTS</h3>
  <p>Aliquam molestie, mi et imperdiet euismod, dui purus auctor tellus, et interdum lacus lectus et ante. Sed accumsan sollicitudin sapien, sit amet adipiscing turpis gravida ac.</p>
</section>

<footer>
  <nav class="footer-nav"><span>Home</span><span>About</span><span>Bio</span><span>Projects</span><span>Contact us</span></nav>
  <p class="copyright">Copyright © 2016. Company Name.All Right Reserved</p>
  <p class="follow">Follow Us</p>
  <div class="social"><span></span><span></span><span></span><span></span><span></span></div>
</footer>
</body>
</html>
```